Velmarotix - world unique technology for better life - please let them know who am i at first sight

We need a new business card for company which is a provider of unique crystal based technology suitable for all living being. For more information and final design you can use our brochure (our colours are black and blue from brochure).
We use Verdana font

Industry/Entity Type

Business

Contact Information for Business Card

regular dimension

Font styles to use
Other font styles liked:
• Verdana

Requirements
Must have
• Logo
• name
• function/position
• phone
• mobile
• e-mail
• adress
Nice to have
• inovative design (technology directed)

```html
<!DOCTYPE html>
<html lang="en">
<head>
<meta charset="utf-8">
<title>Velmarotix Technologies – Business Card</title>
<link rel="stylesheet" href="https://fonts.googleapis.com/css2?family=Ubuntu:wght@300;400;500;700&display=swap">
<style>
  :root {
    --blue: #1fb8e0;
    --blue-deep: #0f9fcf;
    --blue-light: #2ac9ec;
    --white: #ffffff;
    --paper: #f7f9fb;
    --pattern: #dfe7f0;
    --stage: #e9ecef;
  }
  * { margin: 0; padding: 0; box-sizing: border-box; }
  html, body { width: 1200px; height: 858px; overflow: hidden; }
  body {
    background: var(--stage);
    font-family: "Ubuntu", Verdana, sans-serif;
    position: relative;
  }
  .card {
    position: absolute;
    width: 540px;
    height: 318px;
    top: 270px;
    background: var(--white);
    overflow: hidden;
    box-shadow: 0 6px 18px rgba(0,0,0,.12);
  }
  .card--front { left: 40px; }
  .card--back { left: 620px; background: var(--paper); }

  .front-band { position: absolute; inset: 0; }

  .brand {
    position: absolute;
    display: flex;
    align-items: center;
    gap: 10px;
    color: var(--blue);
  }
  .brand__dot {
    width: 40px; height: 40px; border-radius: 50%;
    background: var(--blue);
    flex: none;
  }
  .brand__name {
    font-weight: 300;
    font-size: 28px;
    letter-spacing: 0.5px;
    line-height: 1;
    white-space: nowrap;
  }
  .brand__sub {
    font-weight: 300;
    font-size: 9px;
    letter-spacing: 7.5px;
    margin-top: 5px;
    white-space: nowrap;
  }
  .card--front .brand { left: 30px; top: 128px; }

  .person {
    position: absolute;
    left: 30px;
    bottom: 44px;
    color: var(--blue);
  }
  .person__name { font-weight: 700; font-size: 19px; }
  .person__role { font-weight: 400; font-size: 13px; margin-top: 2px; }

  .contacts {
    position: absolute;
    right: 26px;
    top: 36px;
    color: var(--white);
    text-align: right;
    font-size: 12px;
    line-height: 1.75;
  }
  .contacts ul { list-style: none; }
  .contacts li { display: flex; justify-content: flex-end; align-items: center; gap: 10px; white-space: nowrap; }
  .contacts svg { width: 13px; height: 13px; flex: none; }
  .address { margin-top: 12px; }
  .address li { display: block; }

  .back-pattern { position: absolute; inset: 0; }
  .card--back .brand { left: 70px; top: 100px; gap: 12px; }
  .card--back .brand__dot { width: 64px; height: 64px; }
  .card--back .brand__name { font-size: 44px; letter-spacing: 1px; }
  .card--back .brand__sub { font-size: 12px; letter-spacing: 12px; margin-top: 6px; }
  .web {
    position: absolute;
    left: 70px; bottom: 56px;
    display: flex; align-items: center; gap: 14px;
    color: var(--blue);
    font-size: 15px;
  }
  .web__rule { width: 120px; height: 1px; background: var(--blue); }
</style>
</head>
<body>

<section class="card card--front" aria-label="Business card front">
  <svg class="front-band" viewBox="0 0 540 318" preserveAspectRatio="none" aria-hidden="true">
    <defs>
      <linearGradient id="bandFill" x1="0" y1="0" x2="1" y2="1">
        <stop offset="0" stop-color="#2ac9ec"/>
        <stop offset="1" stop-color="#0f9fcf"/>
      </linearGradient>
    </defs>
    <polygon points="218,0 540,0 540,318 398,318" fill="url(#bandFill)"/>
    <line x1="200" y1="0" x2="380" y2="318" stroke="#1fb8e0" stroke-width="1.5"/>
  </svg>

  <div class="brand">
    <span class="brand__dot"></span>
    <div>
      <div class="brand__name">VELMAROTIX</div>
      <div class="brand__sub">TECHNOLOGIES</div>
    </div>
  </div>

  <div class="person">
    <div class="person__name">Employee Name</div>
    <div class="person__role">Managing Director</div>
  </div>

  <div class="contacts">
    <ul class="contact-list">
      <li>+ xxx(x) xx xxx xxx
        <svg viewBox="0 0 14 14"><rect x="3" y="1" width="8" height="12" rx="1.5" fill="none" stroke="#fff" stroke-width="1.4"/><circle cx="7" cy="10.5" r=".9" fill="#fff"/></svg></li>
      <li>+386(0) 42 519 307
        <svg viewBox="0 0 14 14"><path d="M3 1.5h2.5l1 3-1.5 1a7 7 0 0 0 3.5 3.5l1-1.5 3 1V11a1.5 1.5 0 0 1-1.5 1.5A10 10 0 0 1 1.5 3 1.5 1.5 0 0 1 3 1.5z" fill="#fff"/></svg></li>
      <li>info@velmarotix.eu
        <svg viewBox="0 0 14 14"><rect x="1" y="3" width="12" height="8" fill="none" stroke="#fff" stroke-width="1.4"/><path d="M1 3l6 5 6-5" fill="none" stroke="#fff" stroke-width="1.4"/></svg></li>
      <li>www.velmarotix.eu
        <svg viewBox="0 0 14 14"><circle cx="7" cy="7" r="5.5" fill="none" stroke="#fff" stroke-width="1.4"/><path d="M1.5 7h11M7 1.5c-2.5 3-2.5 8 0 11M7 1.5c2.5 3 2.5 8 0 11" fill="none" stroke="#fff" stroke-width="1"/></svg></li>
    </ul>
    <ul class="address">
      <li>28-34 Harrow Lane</li>
      <li>Leeds LS2 7QT, United Kingdom</li>
    </ul>
  </div>
</section>

<section class="card card--back" aria-label="Business card back">
  <svg class="back-pattern" viewBox="0 0 540 318" preserveAspectRatio="none" role="img" aria-label="Faint crystal lattice decoration across the card">
    <defs>
      <radialGradient id="patternFill" cx="0.7" cy="0.5" r="0.7">
        <stop offset="0" stop-color="#dfe7f0"/>
        <stop offset="1" stop-color="#f7f9fb"/>
      </radialGradient>
    </defs>
    <rect width="540" height="318" fill="url(#patternFill)"/>
  </svg>

  <div class="brand">
    <span class="brand__dot"></span>
    <div>
      <div class="brand__name">VELMAROTIX</div>
      <div class="brand__sub">TECHNOLOGIES</div>
    </div>
  </div>

  <div class="web">
    <span>www.velmarotix.eu</span>
    <span class="web__rule"></span>
  </div>
</section>

</body>
</html>
```